Luxury Wine Label for New Startup Winery

We need a wine label for our new winery startup. We have worked with a local designer but do not feel the resulting label / logo have the elevation required to present our brand as a luxury wine. Our winery is called "Quailbrook Vineyards" and we are focused on extremely high quality hand crafted artisan and estate wines from the Pacific Northwest.
We would like to see designs that utilize a tree line, or other imagery that represents the "Quailbrook" part of our company name. Another interesting feature could be wood grain.
A logo will be required based on your design so please design with this in mind:
This logo should be consistent with the wine bottle label design, and should be representative of our high end exclusive wine while giving a sense of place (Oregon/ Pacific Northwest.)
I will supply an image of the design we received from our local designer, PLEASE NOTE: in general we do like wood grain and tree line concepts but feel the execution was poorly done.
ATTN: Logo design should be suitable for use on: Bottles (Red wine/rose/white wine), Bussiness cards, vehicle signage, business signage, etc
P.S.:
If you have a design that is not outside the box we are still interested in seeing it.
Label is for a burgundy style bottle with a label height of 3.5 - 4" and a width of 3.5-4"
any label <= 4"x4" and >=3.5"x3.5" will be acceptable:
HOWEVER Width should be greater than or equal to height due to the bottle format
Target Market(s)
Wine enthusiasts with adequate discretionary budgets to afford $100 bottles of wine.
Industry/Entity Type
Wine / Winery
Requirements
Must have
- A sense of luxury, a feel of exclusivity, and a theme consistent with our product and brand name
Nice to have
- Tree line, wood grain or other wood themes. Serif fonts
Should not have
- anything cheesy, off topic, hard to read script fonts or anything that makes the label hard to read from a few feet away or too busy

```html
<!DOCTYPE html>
<html lang="en">
<head>
<meta charset="utf-8">
<title>Quailbrook Vineyards – Rosé Label</title>
<link href="https://fonts.googleapis.com/css2?family=Libre+Caslon+Text:wght@400&family=Roboto+Slab:wght@400;500&display=swap" rel="stylesheet">
<style>
  :root {
    --paper: #f6f2e8;
    --label-black: #1b1b1b;
    --white: #ffffff;
    --gold: #c9a447;
    --gold-text: #c6a24a;
    --gold-light: #fbf3a0;
    --gold-deep: #c39b3e;
    --silver-dark: #6e6e6e;
    --silver-light: #fafafa;
    --wood-dark: #3e2a1c;
    --wood-mid: #6b4a31;
    --ink: #2a2214;
  }
  * { box-sizing: border-box; margin: 0; padding: 0; }
  html, body { width: 1200px; height: 1200px; overflow: hidden; }
  body {
    background: var(--paper);
    display: flex;
    flex-direction: column;
    align-items: center;
    padding-top: 90px;
    gap: 30px;
  }
  .front-label {
    width: 960px;
    height: 780px;
    background: var(--label-black);
    display: flex;
    flex-direction: column;
    align-items: center;
    position: relative;
  }
  .silver-band {
    width: 100%;
    height: 60px;
    background: linear-gradient(90deg, var(--silver-dark), #cfcfcf 25%, var(--silver-light) 55%, #cfcfcf 80%, var(--silver-dark));
    flex: none;
  }
  .brand-mark {
    margin-top: 26px;
    width: 148px;
    height: 148px;
    border-radius: 50%;
    border: 5px solid var(--white);
    flex: none;
  }
  .brand-name {
    font-family: "Libre Caslon Text", serif;
    color: var(--white);
    text-align: center;
    margin-top: 22px;
    line-height: 1;
  }
  .brand-name .primary { display: block; font-size: 66px; letter-spacing: 2px; }
  .brand-name .secondary { display: block; font-size: 44px; letter-spacing: 7px; margin-top: 8px; }
  .region {
    font-family: "Roboto Slab", serif;
    font-weight: 500;
    color: var(--gold-text);
    font-size: 32px;
    letter-spacing: 3px;
    margin-top: 34px;
  }
  .wine-type {
    font-family: "Roboto Slab", serif;
    color: var(--white);
    font-size: 32px;
    letter-spacing: 3px;
    margin-top: 6px;
    display: flex;
    align-items: center;
    gap: 22px;
  }
  .wine-type::before, .wine-type::after {
    content: "";
    width: 52px;
    height: 3px;
    background: var(--white);
  }
  .tree-line {
    position: absolute;
    left: 0;
    right: 0;
    top: 515px;
    height: 150px;
    background: linear-gradient(180deg, var(--gold-light), #e8d06a 55%, var(--gold-deep));
  }
  .gold-stripes {
    position: absolute;
    left: 0;
    right: 0;
    top: 665px;
    height: 55px;
    background: linear-gradient(180deg,
      var(--label-black) 0 7px,
      var(--gold) 7px 18px,
      var(--label-black) 18px 25px,
      var(--gold) 25px 44px,
      var(--label-black) 44px 55px);
  }
  .front-label .silver-band:last-child { position: absolute; bottom: 0; }

  .varietal-label {
    width: 960px;
    height: 210px;
    display: flex;
    flex-direction: column;
  }
  .gold-band {
    width: 100%;
    background: linear-gradient(90deg, #e9cf55, var(--gold-light) 30%, #d9b443 60%, var(--gold-light) 85%, #e3c650);
    flex: none;
  }
  .gold-band.top { height: 30px; }
  .gold-band.bottom {
    height: 30px;
    display: flex;
    align-items: center;
    justify-content: center;
    font-family: "Roboto Slab", serif;
    font-weight: 500;
    font-size: 18px;
    letter-spacing: 4px;
    color: var(--ink);
  }
  .wood-panel {
    flex: 1;
    background: linear-gradient(180deg, var(--wood-mid), var(--wood-dark) 50%, var(--wood-mid));
    display: flex;
    align-items: center;
    justify-content: center;
  }
  .varietal {
    font-family: "Libre Caslon Text", serif;
    color: var(--white);
    font-size: 78px;
    letter-spacing: 6px;
  }
</style>
</head>
<body>
  <section class="front-label">
    <div class="silver-band"></div>
    <div class="brand-mark"></div>
    <h1 class="brand-name">
      <span class="primary">QUAILBROOK</span>
      <span class="secondary">VINEYARDS</span>
    </h1>
    <p class="region">“WILLAMETTE VALLEY”</p>
    <p class="wine-type">ROSE WINE</p>
    <div class="tree-line" role="img" aria-label="Gold silhouette of a row of evergreen trees"></div>
    <div class="gold-stripes"></div>
    <div class="silver-band"></div>
  </section>

  <section class="varietal-label">
    <div class="gold-band top"></div>
    <div class="wood-panel" role="img" aria-label="Dark walnut wood grain texture">
      <h2 class="varietal">SYRAH</h2>
    </div>
    <div class="gold-band bottom">ESTATE | 2023 | GROWN</div>
  </section>
</body>
</html>
```